Modern Verdell Tree Care Website

I need a website for a full service Tree Care company. The company provides tree pruning, tree removal, tree preservation, emergency services, stump grinding, and emergency tree services.

Target Market(s)

Customers that need tree services

Industry/Entity Type

Landscaping, Tree Services

Coding

Coded - Design and coding required

Number of Pages Required

5+ page

Font styles to use
Sans Serif

Requirements
Must have
• Good clean design that showcases the services the company provides.
Nice to have
• Services page; contact form, blog, home page, about page

```html
<!DOCTYPE html>
<html lang="en">
<head>
<meta charset="utf-8">
<title>Verdell Tree Care</title>
<link rel="stylesheet" href="https://fonts.googleapis.com/css2?family=Montserrat:wght@600;700&family=Roboto:wght@400;500;700&display=swap">
<style>
:root{
  --green:#8cc63f;
  --orange:#fbb03b;
  --tan:#c49a5e;
  --slate:#5b6770;
  --ink:#1f1f1f;
  --muted:#6b6b6b;
  --about:#5f6d6a;
  --dark:#1a1a1a;
}
*{margin:0;padding:0;box-sizing:border-box}
html,body{width:1200px;height:3003px;overflow:hidden}
body{position:relative;font-family:Roboto,Arial,sans-serif;color:var(--ink);background:#fff}
.abs{position:absolute}
.head{font-family:Montserrat,Arial,sans-serif;font-weight:700;text-transform:uppercase}
.btn{position:absolute;background:var(--orange);color:#fff;font-weight:700;font-size:14px;display:flex;align-items:center;justify-content:center;gap:7px;text-transform:uppercase}
.btn i{width:12px;height:12px;border-radius:50%;background:#fff;display:inline-block;position:relative}
.btn i::after{content:"";position:absolute;left:3px;top:3px;border-left:5px solid var(--orange);border-top:3px solid transparent;border-bottom:3px solid transparent}
/* header */
.brand{left:144px;top:24px;display:flex;align-items:center;gap:12px}
.brand .mark{width:40px;height:40px;background:var(--green)}
.brand span{font-family:Montserrat,sans-serif;font-weight:700;font-size:26px;color:var(--slate)}
.social{top:19px;width:26px;height:26px;border-radius:50%;background:var(--green)}
.nav{top:69px;font-size:14px;font-weight:500;color:var(--ink)}
.callbox{left:0;top:0}
.call-small{left:1000px;top:29px;color:#fff;font-size:12px}
.call-num{left:1000px;top:46px;color:#fff;font-family:Montserrat,sans-serif;font-weight:700;font-size:22px}
/* hero */
.hero{left:0;top:97px;width:1200px;height:568px;background:linear-gradient(100deg,#2f4a22 0%,#4f6e35 40%,#8aa571 65%,#b9cfe0 80%,#dfe8ee 100%)}
.hero-title{left:144px;top:238px;font-size:48px;color:#fff}
.hero-title b{color:var(--green)}
.hero-sub{left:144px;top:307px;color:#fff;font-size:15px;font-weight:500;line-height:27px}
.dot{top:584px;width:11px;height:11px;border-radius:50%;border:2px solid #fff}
/* sections */
.sec-title{left:0;width:1200px;text-align:center;font-size:36px}
.sec-title .a{color:var(--tan)}
.sec-title .b{color:var(--slate)}
.svc{top:793px;width:296px;height:252px}
.svc-label{position:absolute;left:0;right:0;top:182px;text-align:center;color:#fff;font-weight:700;font-size:17px;text-shadow:0 1px 3px rgba(0,0,0,.6)}
.svc-icon{position:absolute;left:110px;top:216px;width:76px;height:76px;border-radius:50%;background:#fff;box-shadow:0 2px 6px rgba(0,0,0,.15)}
.svc-icon::after{content:"";position:absolute;left:8px;top:8px;width:60px;height:60px;border-radius:50%;background:var(--green)}
.about{left:0;top:1250px;width:1200px;height:432px;background:var(--about)}
.about p{font-size:13px;color:#fff;line-height:24px}
.blog{top:1842px;width:288px;height:362px;background:#fff;box-shadow:0 2px 10px rgba(0,0,0,.12);text-align:center}
.blog .img{margin:6px;height:190px}
.blog .date{font-size:13px;color:var(--muted);margin-top:18px}
.blog h3{font-size:16px;font-weight:700;margin-top:11px}
.blog p{font-size:13px;color:var(--muted);line-height:21px;margin-top:10px}
.blog .more{color:var(--orange);font-weight:700;font-size:13px;margin-top:9px}
.round{top:2017px;width:36px;height:36px;border-radius:50%}
.footer{left:0;top:2360px;width:1200px;height:643px;background:var(--dark)}
.field{font-size:13px;color:#fff}
.line{height:1px;background:rgba(255,255,255,.35)}
.info-ic{top:2879px;width:44px;height:44px;border-radius:50%;background:var(--green)}
.info-h{font-size:17px;font-weight:500;color:#fff}
.info-t{font-size:12px;color:#fff}
</style>
</head>
<body>
<!-- header -->
<div class="abs brand"><div class="mark"></div><span>Verdell Tree Care</span></div>
<div class="abs social" style="left:565px"></div>
<div class="abs social" style="left:603px"></div>
<div class="abs social" style="left:640px"></div>
<div class="abs social" style="left:678px"></div>
<div class="btn" style="left:739px;top:13px;width:127px;height:35px;font-size:12px">Get a quote <i></i></div>
<div class="abs nav" style="left:461px">Home</div>
<div class="abs nav" style="left:547px">About Us</div>
<div class="abs nav" style="left:652px">Services</div>
<div class="abs nav" style="left:754px">Blog</div>
<div class="abs nav" style="left:829px">Contact</div>
<svg class="abs callbox" width="1200" height="97" viewBox="0 0 1200 97">
  <polygon points="938,0 1200,0 1200,97 908,97" fill="var(--orange)"/>
  <circle cx="967" cy="49" r="19" fill="none" stroke="#fff" stroke-width="3"/>
  <path d="M959 42c2-3 4-3 5 0l2 3c0 2-2 2-1 4 1 2 3 4 5 5 2 1 2-1 4-1l3 2c3 1 3 3 0 5-5 3-19-9-18-18z" fill="#fff"/>
</svg>
<div class="abs call-small">Call or Text</div>
<div class="abs call-num">(555) 014-2739</div>

<!-- hero -->
<div class="abs hero" role="img" aria-label="Arborist trimming a tall hedge with a pole trimmer under a blue sky"></div>
<div class="abs head hero-title">Verdell <b>Tree</b> Care</div>
<div class="abs hero-sub">We Are More Then Just A Tree Service Company,<br>we Are Stewards Of Our Beautiful Trees.</div>
<div class="btn" style="left:144px;top:387px;width:168px;height:48px">Get started <i></i></div>
<div class="abs dot" style="left:580px"></div>
<div class="abs dot" style="left:594px;border-color:var(--orange)"></div>
<div class="abs dot" style="left:608px"></div>
<svg class="abs" style="left:0;top:600px" width="1200" height="80" viewBox="0 0 1200 80">
  <polygon points="0,56 500,35 1200,65 1200,80 0,80" fill="#fff"/>
  <polygon points="500,35 1200,5 1200,65" fill="var(--green)"/>
</svg>

<!-- services -->
<div class="abs head sec-title" style="top:713px"><span class="a">Our</span> <span class="b">Services</span></div>
<svg class="abs" style="left:65px;top:905px" width="16" height="26"><path d="M13 2 3 13l10 11" fill="none" stroke="#333" stroke-width="2"/></svg>
<svg class="abs" style="left:1119px;top:905px" width="16" height="26"><path d="M3 2l10 11-10 11" fill="none" stroke="#333" stroke-width="2"/></svg>
<div class="abs svc" style="left:144px;background:linear-gradient(160deg,#cfd6d8,#7c8a6e 60%,#5a5f4f)" role="img" aria-label="Arborist in safety gear pruning a pine tree"><div class="svc-label">Tree Pruning</div><div class="svc-icon"></div></div>
<div class="abs svc" style="left:452px;background:linear-gradient(160deg,#6f9a4c,#8aa35a 50%,#6b6b3a)" role="img" aria-label="Worker operating a stump grinder on a lawn"><div class="svc-label">Stump Grinding</div><div class="svc-icon"></div></div>
<div class="abs svc" style="left:759px;background:linear-gradient(160deg,#a59a86,#7d735f 50%,#5d564a)" role="img" aria-label="Worker cutting fallen branches with a chainsaw"><div class="svc-label">Tree Removal</div><div class="svc-icon"></div></div>
<div class="btn" style="left:523px;top:1113px;width:153px;height:46px">Learn more <i></i></div>

<!-- about -->
<div class="abs about"></div>
<div class="abs head" style="left:144px;top:1316px;font-size:36px;color:#fff">About <span style="color:var(--tan)">Us</span></div>
<div class="abs about" style="left:144px;top:1375px;width:500px;height:auto;background:none">
  <p>We are more then just a tree Service Company.We Are Stewards of Our Beautiful Trees.With a passion deeply rooted in arboriculture,we embark on amission to promote the health,beauty,and safety of your trees and landscape.</p>
  <p style="margin-top:8px">Whether its expert tree trimming to enhance aesthetics,meticulous ree removel to mitigate hazards.or Comprehensive tree Health Assessment to ensure safety,We Approach each task with unwavering dedication and attention to detail.</p>
</div>
<div class="btn" style="left:144px;top:1562px;width:139px;height:45px">Read more <i></i></div>
<div class="abs" style="left:706px;top:1290px;width:351px;height:352px;background:linear-gradient(135deg,#a38d55,#7fa54a 50%,#d08a3a)" role="img" aria-label="Arborist at work among green foliage"></div>

<!-- blog -->
<div class="abs head sec-title" style="top:1770px"><span class="a">Latest</span> <span class="b">Blog</span></div>
<div class="abs round" style="left:72px;background:#6e6e6e"></div>
<svg class="abs" style="left:84px;top:2028px" width="12" height="14"><path d="M9 1 3 7l6 6" fill="none" stroke="#fff" stroke-width="2"/></svg>
<div class="abs round" style="left:1092px;background:var(--green)"></div>
<svg class="abs" style="left:1105px;top:2028px" width="12" height="14"><path d="M3 1l6 6-6 6" fill="none" stroke="#fff" stroke-width="2"/></svg>
<div class="abs blog" style="left:144px"><div class="img" style="background:linear-gradient(160deg,#7ea25a,#5d7f3c 60%,#8b6e4b)" role="img" aria-label="Volunteers planting a young tree"></div><div class="date">February 2, 2021</div><h3>Lorem ipsum dolor sit amet,</h3><p>Sed ut perspiciatis unde omnis iste natus<br>sit voluptatem accusantium</p><div class="more">READ MORE ●</div></div>
<div class="abs blog" style="left:456px"><div class="img" style="background:linear-gradient(160deg,#7a9a6a,#6e7b5e 60%,#4e4233)" role="img" aria-label="Two people planting a seedling in soil"></div><div class="date">February 2, 2022</div><h3>Lorem ipsum dolor sit amet,</h3><p>Sed ut perspiciatis unde omnis iste natus<br>sit voluptatem accusantium</p><div class="more">READ MORE ●</div></div>
<div class="abs blog" style="left:767px"><div class="img" style="background:linear-gradient(160deg,#9fa7a0,#5f7a48 55%,#4a4a3a)" role="img" aria-label="Crew clearing a fallen tree on a street"></div><div class="date">February 2, 2023</div><h3>Lorem ipsum dolor sit amet,</h3><p>Sed ut perspiciatis unde omnis iste natus<br>sit voluptatem accusantium</p><div class="more">READ MORE ●</div></div>
<div class="btn" style="left:523px;top:2254px;width:153px;height:46px">Learn more <i></i></div>

<!-- contact -->
<div class="abs footer" role="img" aria-label="Dark photo of an arborist at work"></div>
<svg class="abs" style="left:0;top:2360px" width="1200" height="70" viewBox="0 0 1200 70">
  <polygon points="0,0 700,32 1200,12 0,70" fill="#fff" opacity="0"/>
  <polygon points="0,0 0,0 700,0 1200,0 1200,12 700,32 0,66" fill="#fff"/>
  <polygon points="0,5 700,32 0,62" fill="var(--green)"/>
</svg>
<div class="abs head sec-title" style="top:2458px;color:#fff">Contact <span class="a">Us</span></div>
<div class="abs field" style="left:261px;top:2537px">First name</div>
<div class="abs field" style="left:628px;top:2537px">Last Name</div>
<div class="abs line" style="left:240px;top:2569px;width:352px"></div>
<div class="abs line" style="left:608px;top:2569px;width:352px"></div>
<div class="abs field" style="left:261px;top:2609px">Email</div>
<div class="abs field" style="left:628px;top:2609px">Phone</div>
<div class="abs line" style="left:240px;top:2641px;width:352px"></div>
<div class="abs line" style="left:608px;top:2641px;width:352px"></div>
<div class="abs field" style="left:261px;top:2712px">Message</div>
<div class="abs line" style="left:240px;top:2744px;width:720px"></div>
<div class="btn" style="left:541px;top:2785px;width:119px;height:44px">Submit <i></i></div>

<div class="abs info-ic" style="left:191px"></div>
<svg class="abs" style="left:205px;top:2890px" width="16" height="22"><path d="M8 1a7 7 0 0 1 7 7c0 5-7 13-7 13S1 13 1 8a7 7 0 0 1 7-7z" fill="#fff"/><circle cx="8" cy="8" r="2.5" fill="var(--green)"/></svg>
<div class="abs info-h" style="left:246px;top:2876px">Location:</div>
<div class="abs info-t" style="left:246px;top:2903px">Lorem ipsum dolor sit &nbsp;6514</div>
<div class="abs info-ic" style="left:525px"></div>
<svg class="abs" style="left:538px;top:2892px" width="18" height="18"><path d="M3 2c2-2 3-1 4 1l1 2c0 2-2 2-1 4 1 2 2 3 4 4 2 1 2-1 4-1l2 1c2 1 2 2 0 4-5 3-17-9-14-15z" fill="#fff"/></svg>
<div class="abs info-h" style="left:581px;top:2878px">Phone :</div>
<div class="abs info-t" style="left:580px;top:2905px">(555) 019-9939</div>
<div class="abs info-ic" style="left:810px"></div>
<svg class="abs" style="left:823px;top:2893px" width="18" height="14"><rect x="0" y="0" width="18" height="14" rx="2" fill="#fff"/><path d="M1 1l8 7 8-7" fill="none" stroke="var(--green)" stroke-width="1.5"/></svg>
<div class="abs info-h" style="left:864px;top:2878px">Email :</div>
<div class="abs info-t" style="left:864px;top:2905px">info@verdelltreecare.com</div>
<div class="abs" style="left:0;top:2970px;width:1200px;text-align:center;color:#fff;font-size:12px">Copyright © 2024 Verdell Tree Care. All Rights Reserved.</div>
</body>
</html>
```